Maranoola Wines - web page for new Australian wine label

We need a landing page for our wine company. Maranoola is a family owned company, we grow the gapes, and make the wine in the Clare valley. Daniel Whitlock is the winemaker and is well known for his style, which is all about the fruit flavour rather than wood or age influences. Maranoola is Abriginal for 2 hills and a water source. We hand pick, hand plunge, foot crush resulting in elegant wine. Little to no additives, minimal filtering, single vineyard wines. Handcrafted with small releases of only the best fruit from carefully selected rows and bunches. The Clare valley is located two hours North of Adelaide, is known for cool climate and slow ripening, resulting in wines that have an elegant mouth feel, with bright colour and outstanding flavours. Our Brookmere vineyard has a Eastern aspect, gathering morning sun and escaping the hot afternoons, and in our opinion is on of the prettiest valleys in the world. Only 1000 cases per annum of the very best handpicked fruit, from the best rows. We hope you enjoy the Maranoola style, the reds are lighter in colour, fruit driven palate, more old world influence and the Riesling is on the dry side with fresh citrus. Minimal additives and filtering, our aim was to make wine with minimal influence from wine making. Handcrafted wines.

Target Market(s)

females 18 - 60 are the ones that buy 70 percent of wine, so whilst men are also a target, its the ladies we seek to appeal to.

Industry/Entity Type

It Company

Number of Pages Required

4 page

Font styles to use
Serif

Requirements
Must have
• Eye catching front page that makes me feel like i am ordering from quality company, that cares for what they do. Easy to use ordering, and delivery instructions.
• postage is $14.90 per case Australia wide.
• www.maranoolawines-example.com
Nice to have
• I want to see a fun and family oriented business that cares for the wine, we dont make a lot, its buckets and feet. But its wine made wanting to be the best in the world, we dont cut corners on quality. Handcrafted
Should not have
• dont really have any thoughts here, looking for all ideas

```html
<!DOCTYPE html>
<html lang="en">
<head>
<meta charset="utf-8">
<title>Maranoola Wines</title>
<link href="https://fonts.googleapis.com/css2?family=Lato:wght@400;700&family=Open+Sans:wght@400;600;700&display=swap" rel="stylesheet">
<style>
:root{
  --blue:#0b5cb0;
  --ink:#1d1d1d;
  --body:#555;
  --paper:#e9e6e0;
  --band:#151515;
  --white:#fff;
  --rule:#d9d9d9;
  --footer-text:#555;
}
*{box-sizing:border-box;margin:0;padding:0}
html,body{width:1200px;height:2659px;overflow:hidden;background:var(--white)}
body{position:relative;font-family:"Open Sans",Arial,sans-serif;color:var(--ink)}

/* header */
.site-header{position:absolute;left:0;top:0;width:1200px;height:89px;background:var(--white)}
.brand{position:absolute;left:62px;top:22px;font-family:"Lato",sans-serif;font-size:36px;color:var(--blue);font-weight:400;letter-spacing:1px}
.main-nav a{position:absolute;top:32px;font-family:"Open Sans",sans-serif;font-size:15px;color:var(--ink);text-decoration:none;white-space:nowrap}
.main-nav a.active{color:var(--blue)}
.search-icon{position:absolute;left:1088px;top:35px}

/* hero */
.hero{position:absolute;left:0;top:89px;width:1200px;height:457px;background:linear-gradient(160deg,#3d4a2f 0%,#2a3522 45%,#4b5a3a 75%,#2d3826 100%)}
.hero-name{position:absolute;left:0;width:1200px;top:100px;text-align:center;font-family:"Lato",sans-serif;font-size:70px;color:var(--white);letter-spacing:2px}
.hero-tagline{position:absolute;left:0;width:1200px;top:196px;text-align:center;font-family:"Lato",sans-serif;font-size:28px;color:var(--white)}
.hero-dots{position:absolute;left:560px;top:392px;display:flex;gap:6px}
.hero-dots span{width:16px;height:16px;border-radius:50%;border:2px solid var(--white)}
.hero-dots span.on{background:var(--white)}

/* welcome */
.welcome{position:absolute;left:0;top:546px;width:1200px;height:489px;background:var(--paper)}
.welcome h2{position:absolute;left:99px;top:70px;font-family:"Lato",sans-serif;font-weight:700;font-size:30px;color:var(--ink)}
.welcome .copy{position:absolute;left:99px;top:124px;width:570px;font-size:12px;line-height:27px;color:var(--body)}
.welcome .copy p+p{margin-top:27px}
.btn-outline{position:absolute;display:flex;align-items:center;justify-content:center;border-radius:22px;font-family:"Open Sans",sans-serif;font-weight:700;font-size:14px;text-decoration:none}
.welcome .btn-outline{left:99px;top:370px;width:158px;height:41px;border:1.5px solid var(--blue);color:var(--blue)}
.product-still{position:absolute;left:700px;top:375px;width:500px;height:630px;
  background:radial-gradient(ellipse 50% 55% at 38% 52%,rgba(40,30,24,.85) 0%,rgba(50,38,46,.6) 55%,rgba(60,40,60,0) 100%)}

/* process */
.process{position:absolute;left:0;top:1035px;width:1200px;height:468px}
.process-photo{position:absolute;left:0;top:0;width:597px;height:468px;background:linear-gradient(140deg,#5b1a12 0%,#2a1a24 40%,#3b2a3a 70%,#1d1520 100%)}
.process-panel{position:absolute;left:597px;top:0;width:603px;height:468px;background:var(--blue)}
.process-panel h2{position:absolute;left:64px;top:50px;font-family:"Lato",sans-serif;font-weight:700;font-size:30px;color:var(--white)}
.step{position:absolute;left:64px;width:520px}
.step .num{position:absolute;left:0;top:0;width:71px;height:71px;border-radius:50%;border:2px solid var(--white);display:flex;align-items:center;justify-content:center;font-family:"Lato",sans-serif;font-weight:700;font-size:36px;color:var(--white)}
.step .num.filled{background:var(--white);color:var(--blue)}
.step h3{position:absolute;left:105px;top:4px;font-size:14px;font-weight:700;color:var(--white)}
.step p{position:absolute;left:105px;top:31px;width:360px;font-size:12.5px;line-height:24px;color:var(--white)}

/* mission */
.mission{position:absolute;left:0;top:1510px;width:1200px;height:450px;background:linear-gradient(180deg,#2f3128 0%,#26271f 50%,#3a3a2c 100%)}
.mission-frame{position:absolute;left:101px;top:48px;width:998px;height:351px;border:2px solid rgba(255,255,255,.75)}
.mission h2{position:absolute;left:0;width:1200px;top:96px;text-align:center;font-family:"Lato",sans-serif;font-weight:700;font-size:30px;color:var(--white)}
.mission p{position:absolute;left:280px;width:640px;top:154px;text-align:center;font-size:14px;line-height:30px;color:var(--white)}
.mission .btn-outline{left:526px;top:305px;width:148px;height:43px;border:1.5px solid var(--white);color:var(--white);font-size:15px}

/* offer */
.offer{position:absolute;left:0;top:1964px;width:1200px;height:298px;background:var(--band)}
.offer-photo{position:absolute;left:0;top:0;width:346px;height:298px;background:linear-gradient(135deg,#1d3a18 0%,#2f6a2a 45%,#d9ddd3 70%,#1a2a16 100%)}
.offer-text{position:absolute;left:393px;top:66px;font-family:"Lato",sans-serif;font-weight:700;font-size:20px;line-height:44px;color:var(--white)}
.offer-text .price{font-size:30px}
.offer .btn-outline{left:393px;top:179px;width:206px;height:42px;border:1.5px solid var(--white);color:var(--white);font-size:16px}

/* footer */
.site-footer{position:absolute;left:0;top:2262px;width:1200px;height:397px;background:var(--white)}
.footer-col{position:absolute;top:55px}
.footer-col h4{font-family:"Open Sans",sans-serif;font-weight:400;font-size:18px;color:var(--ink);margin-bottom:16px}
.footer-col ul{list-style:none}
.footer-col li{font-size:13px;color:var(--footer-text);height:32px}
.divider{position:absolute;top:47px;width:1px;height:181px;background:var(--rule)}
.sub-note{font-size:13px;color:var(--footer-text)}
.sub-form{position:absolute;left:0;top:87px;display:flex}
.sub-form .field{width:229px;height:37px;border:1px solid #bbb;font-size:12px;color:#888;padding:10px 12px}
.sub-form .go{width:94px;height:37px;background:var(--blue);color:var(--white);font-size:12px;font-weight:700;display:flex;align-items:center;justify-content:center}
.stay{position:absolute;left:0;top:150px;font-size:18px;color:var(--ink)}
.social{position:absolute;left:0;top:190px;display:flex;gap:7px}
.social span{width:35px;height:35px;border-radius:50%;background:var(--blue)}
.footer-rule{position:absolute;left:99px;top:316px;width:1002px;height:1px;background:var(--rule)}
.copyright{position:absolute;left:0;width:1200px;top:348px;text-align:center;font-size:12.5px;color:var(--footer-text)}
</style>
</head>
<body>

<header class="site-header">
  <div class="brand">Maranoola</div>
  <nav class="main-nav">
    <a class="active" style="left:434px">Home</a>
    <a style="left:505px">Our Family</a>
    <a style="left:611px">Our Wineries</a>
    <a style="left:731px">Our Passions</a>
    <a style="left:852px">Find Our Wine</a>
    <a style="left:982px">Contact Us</a>
  </nav>
  <svg class="search-icon" width="18" height="18" viewBox="0 0 18 18"><circle cx="7.5" cy="7.5" r="5.5" fill="none" stroke="#1d1d1d" stroke-width="2.4"/><line x1="11.5" y1="11.5" x2="16.5" y2="16.5" stroke="#1d1d1d" stroke-width="2.6" stroke-linecap="round"/></svg>
</header>

<section class="hero" role="img" aria-label="Vineyard foliage with bunches of dark grapes on the vine">
  <div class="hero-name">Maranoola</div>
  <div class="hero-tagline">We are a family owned wine company</div>
  <div class="hero-dots"><span class="on"></span><span></span><span></span><span></span></div>
</section>

<section class="welcome">
  <h2>Welcome to Maranoola</h2>
  <div class="copy">
    <p>At vero eos et accusamus et iusto odio dignissimos ducimus qui blanditiis praesentium voluptatum deleniti atque corrupti quos dolores et quas molestias.</p>
    <p>Excepturi sint occaecati cupiditate non provident, similique sunt in culpa qui officia deseru mollitia animi, id est laborum et dolorum fuga. Et harum quidem rerum facilis est et expedita distinct libero tempore, cum soluta nobis est eligendi optio cumque nihil impedit quo minus id quod maxime plac eat facere possimus, omnis voluptas assumenda est, omnis dolor repellendus. Temporibus autem quibusdam et aut officiis debitis aut rerum necessit.</p>
  </div>
  <a class="btn-outline">READ MORE &gt;&gt;</a>
</section>
<div class="product-still" role="img" aria-label="Bottle of Maranoola Riesling beside a bunch of dark red grapes with a vine leaf"></div>

<section class="process">
  <div class="process-photo" role="img" aria-label="Hands plunging crushed red grapes in a vat"></div>
  <div class="process-panel">
    <h2>The Wine Making Process</h2>
    <div class="step" style="top:118px"><div class="num filled">1</div><h3>HAND PICK</h3><p>At vero eos et accusamus et iusto odio dignissimos ducimus qui blanditiis praesentium voluptatum dele.</p></div>
    <div class="step" style="top:227px"><div class="num">2</div><h3>HAND PLUNGE</h3><p>At vero eos et accusamus et iusto odio dignissimos ducimus qui blanditiis praesentium voluptatum dele.</p></div>
    <div class="step" style="top:339px"><div class="num">3</div><h3>FOOT CRUSH</h3><p>At vero eos et accusamus et iusto odio dignissimos ducimus qui blanditiis praesentium voluptatum dele.</p></div>
  </div>
</section>

<section class="mission" role="img" aria-label="Dusk view of the vineyard rows and winery buildings">
  <div class="mission-frame"></div>
  <h2>Our Mission</h2>
  <p>Nemo enim ipsam voluptatem quia voluptas sit aspernatur aut odit aut fugit, sed quia consequuntur magni dolores eos qui ratione voluptatem sequi nesc que porro quisquam est, qui dolorem ipsum quia dolor sit amet, consectetur, adipisci velit, sed quia non numquam eius modi tempora incidunt ut labore et dolore magnam aliquam quaerat</p>
  <a class="btn-outline">ABOUT US</a>
</section>

<section class="offer">
  <div class="offer-photo" role="img" aria-label="White lily of the valley flowers against a green leaf"></div>
  <div class="offer-text">Only 1000 cases per annum of the very best handpicked fruit, from the best rows.<br>Delivery charge is <span class="price">$14.90</span> per case Australia wide.</div>
  <a class="btn-outline">BUY NOW!</a>
</section>

<footer class="site-footer">
  <div class="footer-col" style="left:99px"><h4>Information</h4><ul><li>About Us</li><li>Careers</li><li>Privacy &amp; Security</li><li>Site Map</li><li>Terms of Use</li></ul></div>
  <div class="divider" style="left:259px"></div>
  <div class="footer-col" style="left:303px"><h4>Help &amp; support</h4><ul><li>Login</li><li>New Customers</li><li>Products</li><li>Frequently Asked Questions</li><li>How to Order</li></ul></div>
  <div class="divider" style="left:507px"></div>
  <div class="footer-col" style="left:551px"><h4>My Account</h4><ul><li>Delivery Information</li><li>My Account</li><li>Order Tracking</li><li>Reminder Service</li><li>Shipping, Returns &amp; Fees</li></ul></div>
  <div class="divider" style="left:732px"></div>
  <div class="footer-col" style="left:778px;width:330px;height:240px">
    <h4>Email Subscription</h4>
    <div class="sub-note">Register your email address to get information about</div>
    <div class="sub-form"><div class="field">Email Address</div><div class="go">SUBSCRIBE</div></div>
    <div class="stay">Stay Connected</div>
    <div class="social"><span></span><span></span><span></span><span></span><span></span><span></span><span></span></div>
  </div>
  <div class="footer-rule"></div>
  <div class="copyright">Copyrights © 2017, Maranoola. All Rights Reserved &nbsp;|&nbsp; Privacy Policy | Terms of Use | Feedback</div>
</footer>

</body>
</html>
```